Business Card Design Project

Business Card
We are rebranding with a new logo
Industry/Entity Type
Business
Contact Information for Business Card
Dennis Morvale +61 487215963 dennis@quorv.com.au P.O. Box 872 Fernlow QLD 4309
Requirements
Must have
- Logo

```html
<!DOCTYPE html>
<html lang="en">
<head>
<meta charset="utf-8">
<title>Quorv International – Business Card</title>
<link rel="stylesheet" href="https://fonts.googleapis.com/css2?family=Source+Sans+3:wght@400;600;700&display=swap">
<style>
  :root {
    --backdrop: #262626;
    --card-white: #f3f3f3;
    --blue-light: #0ea3da;
    --blue-deep: #0a668f;
    --orange-light: #f08a1c;
    --orange-deep: #d9531e;
    --brand-blue: #1479a8;
    --text-white: #ffffff;
  }
  html, body {
    margin: 0;
    width: 1200px;
    height: 915px;
    overflow: hidden;
    background: var(--backdrop);
  }
  .card {
    position: absolute;
    left: 80px;
    top: 160px;
    width: 1040px;
    height: 595px;
    background: var(--card-white);
    overflow: hidden;
    font-family: "Source Sans 3", "Myriad Pro", sans-serif;
  }
  .card-shapes {
    position: absolute;
    inset: 0;
    width: 100%;
    height: 100%;
  }
  .brand {
    position: absolute;
    left: 600px;
    top: 150px;
    width: 360px;
    text-align: center;
    color: var(--brand-blue);
    font-weight: 600;
    line-height: 1;
  }
  .brand-name {
    display: block;
    font-size: 96px;
    letter-spacing: 1px;
  }
  .brand-sub {
    display: block;
    margin-top: 14px;
    font-size: 29px;
    letter-spacing: 5px;
  }
  .contact {
    position: absolute;
    left: 54px;
    top: 318px;
    color: var(--text-white);
  }
  .contact-name {
    margin: 0 0 24px;
    font-size: 28px;
    font-weight: 700;
    letter-spacing: 0.3px;
  }
  .contact-address {
    margin: 0 0 16px;
    font-size: 24px;
    line-height: 32px;
    font-style: normal;
  }
  .contact-list {
    list-style: none;
    margin: 0;
    padding: 0;
    font-size: 24px;
    line-height: 33px;
  }
  .contact-list li {
    display: flex;
    align-items: center;
  }
  .contact-icon {
    width: 22px;
    height: 22px;
    margin-right: 17px;
    fill: var(--text-white);
  }
</style>
</head>
<body>
  <div class="card">
    <svg class="card-shapes" viewBox="0 0 1040 595" aria-hidden="true">
      <defs>
        <radialGradient id="blue-panel" cx="0.42" cy="0.38" r="0.75">
          <stop offset="0" stop-color="var(--blue-light)"/>
          <stop offset="1" stop-color="var(--blue-deep)"/>
        </radialGradient>
      </defs>
      <path class="swoosh-light" d="M0 0 H875 C600 8 432 98 428 222 C432 335 585 480 690 595 H0 Z" fill="var(--orange-light)"/>
      <path class="swoosh-deep" d="M0 0 H790 C560 10 400 100 396 222 C400 335 570 480 684 595 H0 Z" fill="var(--orange-deep)"/>
      <path class="blue-panel" d="M0 0 H700 C520 16 360 112 360 222 C362 335 560 480 676 595 H0 Z" fill="url(#blue-panel)" stroke="#ffffff" stroke-width="4"/>
    </svg>

    <div class="brand">
      <span class="brand-name">Quorv</span>
      <span class="brand-sub">INTERNATIONAL</span>
    </div>

    <div class="contact">
      <p class="contact-name">DENNIS MORVALE</p>
      <address class="contact-address">P.O. Box 872<br>Fernlow QLD 4309</address>
      <ul class="contact-list">
        <li>
          <svg class="contact-icon" viewBox="0 0 24 24" aria-hidden="true"><path d="M3 8 C3 4 21 4 21 8 L21 10 L16 10 L16 8 L8 8 L8 10 L3 10 Z M6 12 L18 12 L21 20 L3 20 Z"/><circle cx="12" cy="16" r="2.2" fill="#0d7fb0"/></svg>
          +61 487215963
        </li>
        <li>
          <svg class="contact-icon" viewBox="0 0 24 24" aria-hidden="true"><path d="M2 6 H22 V18 H2 Z"/><path d="M2 6 L12 13 L22 6" fill="none" stroke="#0d7fb0" stroke-width="1.6"/></svg>
          dennis@quorv.com.au
        </li>
        <li>
          <svg class="contact-icon" viewBox="0 0 24 24" aria-hidden="true"><circle cx="12" cy="12" r="9"/><path d="M7 8 C9 7 11 9 10 11 C9 13 7 12 6 14 M14 5 C15 8 17 8 18 10 M13 14 C15 14 16 16 15 19" fill="none" stroke="#0d7fb0" stroke-width="1.8"/></svg>
          www.quorv.com.au
        </li>
      </ul>
    </div>
  </div>
</body>
</html>
```